Mandala-like Graphic for Ecosystem of Well-Being

I have created a simple graphic for a framework I use with clients and potential clients. I would like it to look more polished, professional, and customized. (As opposed to non-graphic designer created it on Canva or Powrepoint) I would like to possibly integrate my brand colors---or one of my brand colors. https://tintharborly.net/swatch-board-5817/ The dark blue is the one to definitely use. I do not want it looking to feminine. I do want different colors for the 5 elements: Purpose, Mental, Physical, Emotional, Social.

Target Market(s)

Working professionals.

Font styles to use
Serif
Other font styles liked:
• Playfair Display

Requirements
Must have
• 4 Overlapping circles with one circle in center that says Purpose
Other 4 circles labeled Physical, Emotional, Mental, Social
Mandala-like design

**I added an attachment with colors I use when marketing this course.**
Nice to have
• Playfair Display font

```html
<!DOCTYPE html>
<html lang="en">
<head>
<meta charset="utf-8">
<title>Ecosystem of Well-Being</title>
<link rel="stylesheet" href="https://fonts.googleapis.com/css2?family=Playfair+Display:wght@700&display=swap">
<style>
  :root {
    --canvas-bg: #fefefe;
    --ring-pink: #ffa9d3;
    --physical-fill: #fdd0e5;
    --physical-line: #dc6797;
    --mental-fill: #fe99c6;
    --mental-line: #dd3a7d;
    --emotional-fill: #c96785;
    --emotional-line: #a90036;
    --social-fill: #66789a;
    --social-line: #42103f;
    --purpose-fill: #3d2a55;
    --purpose-line: #4a1840;
    --label-fill: #ffffff;
    --label-edge: #1a1a1a;
  }
  html, body {
    margin: 0;
    padding: 0;
    overflow: hidden;
    background: var(--canvas-bg);
  }
  .canvas {
    width: 1200px;
    height: 1200px;
    position: relative;
    background: var(--canvas-bg);
    overflow: hidden;
  }
  .mandala {
    display: block;
    width: 1200px;
    height: 1200px;
  }
  .ring { fill: none; stroke: var(--ring-pink); stroke-width: 22; opacity: 0.85; }
  .element { stroke-width: 24; }
  .element--physical { fill: var(--physical-fill); stroke: var(--physical-line); opacity: 0.95; }
  .element--mental { fill: var(--mental-fill); stroke: var(--mental-line); opacity: 0.95; }
  .element--emotional { fill: var(--emotional-fill); stroke: var(--emotional-line); opacity: 0.95; }
  .element--social { fill: var(--social-fill); stroke: var(--social-line); opacity: 0.95; }
  .element--purpose { fill: var(--purpose-fill); stroke: var(--purpose-line); fill-opacity: 0.72; stroke-opacity: 0.85; }
  .label {
    font-family: "Playfair Display", "Times New Roman", serif;
    font-weight: 700;
    font-size: 56px;
    letter-spacing: 1px;
    fill: var(--label-fill);
    stroke: var(--label-edge);
    stroke-width: 1.6;
    paint-order: stroke fill;
    text-anchor: middle;
    dominant-baseline: middle;
  }
</style>
</head>
<body>
<main class="canvas">
  <svg class="mandala" viewBox="0 0 1200 1200" xmlns="http://www.w3.org/2000/svg" role="img" aria-label="Ecosystem of Well-Being: Purpose at the centre of Physical, Mental, Emotional and Social">
    <g class="elements">
      <circle class="element element--physical" cx="376" cy="365" r="210"/>
      <circle class="element element--mental" cx="824" cy="365" r="210"/>
      <circle class="element element--emotional" cx="376" cy="823" r="210"/>
      <circle class="element element--social" cx="824" cy="823" r="210"/>
    </g>
    <g class="rings">
      <circle class="ring" cx="600" cy="283" r="210"/>
      <circle class="ring" cx="283" cy="600" r="210"/>
      <circle class="ring" cx="917" cy="600" r="210"/>
      <circle class="ring" cx="600" cy="917" r="210"/>
    </g>
    <circle class="element element--purpose" cx="600" cy="600" r="212"/>
    <g class="labels">
      <text class="label" x="376" y="345">PHYSICAL</text>
      <text class="label" x="824" y="345">MENTAL</text>
      <text class="label" x="600" y="600">PURPOSE</text>
      <text class="label" x="376" y="857">EMOTIONAL</text>
      <text class="label" x="824" y="857">SOCIAL</text>
    </g>
  </svg>
</main>
</body>
</html>
```